Detail Shop Business card design

i need a business card design for my new detailing company called 'Brisk's Polish Works'. i want an all black and white design . simple, direct and to the point. i want the designer to choose a fitting font to match the logothe front should have logo, address, phone and email and the back side should have a slogan and text indicating that we offer services on anything including cars, trucks, motorcycles and RVs. slogan will read "we take pride in your ride"
maybe also very small on the back side the IG icon with Brisks_Polish_Works

phone 208.417.6352
address 3847 E Larkin Ave
Spokane WA 99214
email: BrisksPolish@mailvexo.com

Target Market(s)

all ages , auto enthusiasts

Industry/Entity Type

Automotive

Contact Information for Business Card

the front should have logo, address, phone and email and the back side should have a slogan and text indicating that we offer services on anything including cars, trucks, motorcycles and RVs. slogan will read "we take pride in your ride"

phone 208.417.6352
address 3847 E Larkin Ave
Spokane WA 99214

Colors
000000
ffffff

Requirements
Must have
• bold font and very simple design with good spacing
Nice to have
• anything creative from the designer indicating we service any types of vehicles
Should not have
• any colors ,

```html
<!DOCTYPE html>
<html lang="en">
<head>
<meta charset="utf-8">
<title>Brisk's Polish Works – Business Card</title>
<link href="https://fonts.googleapis.com/css2?family=Roboto:wght@400;500;700&family=Pathway+Gothic+One&display=swap" rel="stylesheet">
<style>
  :root {
    --ink: #000000;
    --paper: #ffffff;
    --card-tint: #f4f4f4;
    --backdrop: #e6e6e6;
    --shade: rgba(0,0,0,0.18);
  }
  * { margin: 0; padding: 0; box-sizing: border-box; }
  html, body { width: 1200px; height: 960px; overflow: hidden; }
  body {
    background: var(--backdrop);
    position: relative;
    font-family: "Roboto", Arial, sans-serif;
    color: var(--ink);
  }
  .card {
    position: absolute;
    width: 599px;
    height: 343px;
    background: var(--card-tint);
    box-shadow: 0 3px 8px var(--shade);
    overflow: hidden;
  }
  .card--front { left: 314px; top: 113px; }
  .card--back  { left: 311px; top: 472px; }

  /* front */
  .brand {
    position: absolute;
    left: 150px; top: 30px; width: 300px;
    display: flex; flex-direction: column; align-items: center; gap: 14px;
  }
  .brand__mark {
    width: 92px; height: 92px; border-radius: 50%;
    background: var(--ink);
  }
  .brand__name {
    font-weight: 700; font-size: 26px; letter-spacing: 0.5px;
    color: var(--ink); white-space: nowrap;
  }
  .mini-car {
    position: absolute; left: 26px; top: 162px;
    width: 138px; height: 50px;
    background: linear-gradient(180deg, #2a2a2a, #000);
    border-radius: 18px 18px 4px 4px;
  }
  .info-band {
    position: absolute; left: 0; top: 214px;
    width: 100%; height: 129px;
    background: var(--ink); color: var(--paper);
  }
  .person { position: absolute; left: 37px; top: 24px; }
  .person__name { font-size: 21px; font-weight: 500; letter-spacing: 0.3px; }
  .person__title { font-size: 14.5px; margin-top: 2px; }
  .person__address { font-size: 14.5px; line-height: 19px; margin-top: 10px; }
  .contacts {
    position: absolute; right: 28px; top: 30px;
    list-style: none; text-align: right;
  }
  .contacts li {
    font-size: 14.5px; line-height: 19.5px;
    display: flex; justify-content: flex-end; align-items: center; gap: 9px;
  }
  .contacts svg { width: 12px; height: 12px; fill: var(--paper); flex: none; }

  /* back */
  .hero-car {
    position: absolute; left: 114px; top: 88px;
    width: 380px; height: 140px;
    background: radial-gradient(ellipse at 45% 55%, #1a1a1a 0%, #000 60%, #3a3a3a 100%);
    border-radius: 60px 60px 10px 10px;
  }
  .slogan {
    position: absolute; left: 0; top: 271px; width: 100%;
    text-align: center;
    font-weight: 700; font-size: 17px; letter-spacing: 0.4px;
  }
  .slogan-rule {
    position: absolute; left: 137px; top: 293px;
    width: 324px; height: 1.5px; background: var(--ink);
  }
  .services {
    position: absolute; left: 0; top: 297px; width: 100%;
    text-align: center;
    font-family: "Pathway Gothic One", "Arial Narrow", sans-serif;
    font-size: 16px;
  }
</style>
</head>
<body>

<section class="card card--front" aria-label="Card front">
  <div class="brand">
    <span class="brand__mark"></span>
    <span class="brand__name">Brisk's Polish Works</span>
  </div>
  <div class="mini-car" role="img" aria-label="Small black hot rod silhouette"></div>

  <div class="info-band">
    <div class="person">
      <p class="person__name">DALE HARMON</p>
      <p class="person__title">CEO/FOUNDER</p>
      <p class="person__address">3847 E Larkin Ave<br>Spokane WA 99214</p>
    </div>
    <ul class="contacts">
      <li>208.417.6352
        <svg viewBox="0 0 24 24" aria-hidden="true"><path d="M6.6 10.8a15.1 15.1 0 0 0 6.6 6.6l2.2-2.2a1 1 0 0 1 1-.25 11.4 11.4 0 0 0 3.6.57 1 1 0 0 1 1 1V20a1 1 0 0 1-1 1A17 17 0 0 1 3 4a1 1 0 0 1 1-1h3.5a1 1 0 0 1 1 1c0 1.25.2 2.45.57 3.57a1 1 0 0 1-.25 1z"/></svg></li>
      <li>208 731 5582
        <svg viewBox="0 0 24 24" aria-hidden="true"><path d="M7 1h10a2 2 0 0 1 2 2v18a2 2 0 0 1-2 2H7a2 2 0 0 1-2-2V3a2 2 0 0 1 2-2zm0 3v14h10V4zm5 15.5a1 1 0 1 0 0 2 1 1 0 0 0 0-2z"/></svg></li>
      <li>BrisksPolish@mailvexo.com
        <svg viewBox="0 0 24 24" aria-hidden="true"><path d="M2 5h20v14H2zm2 2v.5l8 5 8-5V7zm0 3v7h16v-7l-8 5z"/></svg></li>
      <li>www.briskspolish.com
        <svg viewBox="0 0 24 24" aria-hidden="true"><path d="M12 2a10 10 0 1 0 0 20 10 10 0 0 0 0-20zm-1 17.9A8 8 0 0 1 4.2 10.5L9 15v1a2 2 0 0 0 2 2zm6.9-2.5A2 2 0 0 0 16 16h-1v-3a1 1 0 0 0-1-1H8v-2h2a1 1 0 0 0 1-1V7h2a2 2 0 0 0 2-2v-.4a8 8 0 0 1 2.9 12.8z"/></svg></li>
    </ul>
  </div>
</section>

<section class="card card--back" aria-label="Card back">
  <div class="hero-car" role="img" aria-label="Large black and white hot rod illustration"></div>
  <p class="slogan">WE TAKE PRIDE IN YOUR RIDE</p>
  <div class="slogan-rule"></div>
  <p class="services">we offer services on anything including cars, trucks, motorcycles &amp; RVs</p>
</section>

</body>
</html>
```